Emerging automotive detailing business

I am starting a small automotive detailing business in hopes of becoming a well-known detailer to work on high end cars. I would like a card to reflect the high quality and time I put into my work. The name of the company is Bright Crest Detailing. I feel like it represents racecars getting off the line at the drag strip as well as an innuendo of "Up the Ladder". I do minor paint correction such as clay barring, multi-step buffing and polishing, waxing, hand washes, etc. I am always striving to learn more and improve my work. My goal is to have total customer satisfaction. This is a female run business but I do not want it to be very girly. Elegant is okay! I have pictures of my personal wrenfield attached, they do not need to be incorporated but if you can think of a cool way to use 1 or all of them, go for it!

Target Market(s)

Anyone that owns a vehicle. Preferably high end vehicles such as Valtori, Castellverde and Morvani but I will also happily work on any car, truck or suv no matter what brand.

Industry/Entity Type

Automotive

Contact Information for Business Card

Bright Crest Detailing
Mira Tolland
4175 Quenhollow Rd
Ashmere PA 17492
Cell phone- call/text- 717-555-0148
email- brightcrestdetails@maildrop-example.com
Instagram: @brightcrestdetailing
Facebook: facebook.com/brightcrestdetailing

Requirements
Must have
• Business name, my name, address, phone number. Listing that I do minor paint correction such as clay barring, multi-step buffing and polishing, waxing, hand washes, interior cleaning, and more. (This last part was in nice to haves but I have realized that I do really want it, so I moved it to must haves.) I want something that is different and eye-catching to my customers. Some people have done this very well with cards already submitted to me, but a lot have not. I didn't mess with the "look and feel bars" much because because I am pretty open to the overall design as long as it is not your basic run of the mill design.
Nice to have
• Something car related. Maybe an appointment time/date line. I do not have a logo, but if you would like to design one and incorporate it, that would be amazing!
Should not have
• Purple and Pink colors. Boring, basic, normal card.

```html
<!DOCTYPE html>
<html lang="en">
<head>
<meta charset="utf-8">
<title>Bright Crest Detailing – Business Card</title>
<link rel="stylesheet" href="https://fonts.googleapis.com/css2?family=Open+Sans:wght@400&family=Tinos:wght@400&display=swap">
<style>
  :root {
    --page-bg: #e9e7e3;
    --card-white: #ffffff;
    --field-green: #6b8540;
    --name-teal: #2f7f96;
    --ink: #1f1f1f;
    --muted-ink: #4a4a4a;
    --divider-grey: #c9c9c9;
    --car-tone-light: #f4f4f4;
    --car-tone-dark: #8f8f8f;
    --card-shadow: 0 10px 28px rgba(0, 0, 0, 0.18);
  }
  * { box-sizing: border-box; margin: 0; padding: 0; }
  html, body {
    width: 1200px;
    height: 676px;
    overflow: hidden;
    background: var(--page-bg);
  }
  .canvas {
    width: 1200px;
    height: 676px;
    display: flex;
    align-items: center;
    justify-content: center;
    gap: 60px;
  }
  .card {
    position: relative;
    width: 525px;
    height: 300px;
    background: var(--card-white);
    box-shadow: var(--card-shadow);
    overflow: hidden;
  }

  /* Front side */
  .card-front .field-band {
    position: absolute;
    inset: 0;
    width: 100%;
    height: 100%;
  }
  .card-front .car-illustration {
    position: absolute;
    left: 150px;
    top: 70px;
    width: 230px;
    height: 78px;
    border-radius: 55% 45% 18% 18% / 75% 75% 25% 25%;
    background: linear-gradient(180deg, var(--car-tone-light) 0%, var(--car-tone-dark) 100%);
  }
  .card-front .business-name {
    position: absolute;
    right: 28px;
    top: 26px;
    font-family: "Open Sans", Arial, sans-serif;
    font-size: 17px;
    color: var(--name-teal);
    white-space: nowrap;
  }

  /* Back side */
  .card-back .contact-layout {
    position: absolute;
    left: 36px;
    top: 34px;
    display: flex;
    align-items: stretch;
    gap: 14px;
  }
  .card-back .owner-name {
    font-family: "Open Sans", Arial, sans-serif;
    font-size: 17px;
    color: var(--name-teal);
    line-height: 1.2;
    padding-top: 2px;
    white-space: nowrap;
  }
  .card-back .divider-bar {
    width: 9px;
    background: linear-gradient(180deg, var(--divider-grey) 0%, rgba(201, 201, 201, 0.15) 100%);
  }
  .card-back .contact-details {
    font-family: "Tinos", "Times New Roman", serif;
    font-size: 15.5px;
    color: var(--ink);
    line-height: 1.3;
    list-style: none;
  }
  .card-back .service-list {
    position: absolute;
    left: 36px;
    right: 36px;
    bottom: 30px;
    font-family: "Tinos", "Times New Roman", serif;
    font-size: 13.5px;
    line-height: 1.35;
    color: var(--muted-ink);
  }
</style>
</head>
<body>
  <main class="canvas">
    <section class="card card-front" aria-label="Business card front">
      <svg class="field-band" viewBox="0 0 525 300" preserveAspectRatio="none" aria-hidden="true">
        <path d="M0 118 C 120 95, 300 150, 420 200 C 470 222, 505 245, 525 262 L 525 300 L 0 300 Z" fill="var(--field-green)"/>
      </svg>
      <div class="car-illustration" role="img" aria-label="Illustration of a white sports car cresting the green hill"></div>
      <p class="business-name">Bright Crest Detailing</p>
    </section>

    <section class="card card-back" aria-label="Business card back">
      <div class="contact-layout">
        <p class="owner-name">Mira Tolland</p>
        <span class="divider-bar" aria-hidden="true"></span>
        <ul class="contact-details">
          <li>4175 Quenhollow Rd</li>
          <li>Ashmere PA 17492</li>
          <li>Cell phone- call/text- 717-555-0148</li>
          <li>email- brightcrestdetails@maildrop-example.com</li>
          <li>Instagram: @brightcrestdetailing</li>
        </ul>
      </div>
      <p class="service-list">Minor paint correction · clay barring · multi-step buffing &amp; polishing · waxing · hand washes · interior cleaning &amp; more</p>
    </section>
  </main>
</body>
</html>
```